Equipment Finance Specialist I work with companies who need the funds to buy their equipment

I would like a business card that stands out on the shelves. I want to be able to hand it to someone and say WOW. This card should have my logo.
You can put color into it I am very open on design and color

What my company does is we deal with dealerships that sell equipment such as Dump Trucks garbage trucks tractors trailers. Customers get referred to us and depending on their time in business we will ask for the following items

Companies that have been in business for more than two years we have a credit application program up to 250K . With this program we need the following items Credit application filled out(which is what I would like to be able for the customer to click on my website to get.) as well as three current month bank statements.

Deals over 250k we will need the following items

2 years business tax returns
2 years personal tax returns
Profit & Loss statement
Personal Financial Statement

what we do
100% FINANCING
SEASONAL PAYMENTS
LOAN BALLOON PAYMENTS
TRAC LEASING
LOW-INTEREST REFINANCING RATES
DEBT CONSOLIDATION

We specialize in creative financing solutions and offer a variety of reliable, flexible and expandable lending choices.

Target Market(s)

Trucking Companies

Industry/Entity Type

Trucking Company

Contact Information for Business Card

* $250,000 Application only Program
* Loans from $30,000 to 5,000,000
* Competitive Interest Rates

Font styles to use
Serif
Sans Serif

Colors

Designer to choose colors to be used in the design.

Requirements
Must have
• On the back of the card.
• * $250,000 Application only Program
• * Loans from $30,000 to 5,000,000
• My name, email, website. address
• * Competitive Interest Rates
• * 100% Financing
Nice to have
• I want my logo to pop on the card
• My logo is the great one I would like to use
Should not have
• I am up for your creativity as well

```html
<!DOCTYPE html>
<html lang="en">
<head>
<meta charset="utf-8">
<title>Ridgeline Funding – Business Card</title>
<link rel="stylesheet" href="https://fonts.googleapis.com/css2?family=Oswald:wght@600;700&family=Work+Sans:wght@400;500&display=swap">
<style>
  :root {
    --backdrop: #1e1e1f;
    --card: #0f0f10;
    --card-edge: #1a1a1b;
    --gloss-text: #55555a;
    --gloss-hi: #2c2c2e;
    --silver: #d9d9db;
    --silver-soft: #a9a9ad;
    --muted: #6e6e72;
  }
  * { box-sizing: border-box; margin: 0; padding: 0; }
  html, body { width: 1200px; height: 900px; overflow: hidden; }
  body {
    background: var(--backdrop);
    display: flex;
    flex-direction: column;
    align-items: center;
    justify-content: center;
    gap: 34px;
    font-family: "Work Sans", sans-serif;
  }
  .card {
    width: 680px;
    height: 400px;
    background: var(--card);
    border: 1px solid var(--card-edge);
    position: relative;
    overflow: hidden;
  }
  /* Front */
  .brand {
    position: absolute;
    left: 50%;
    top: 44%;
    transform: translate(-50%, -50%);
    display: flex;
    align-items: center;
    gap: 20px;
  }
  .brand-dot {
    flex: none;
    width: 64px;
    height: 64px;
    border-radius: 50%;
    background: var(--gloss-hi);
  }
  .brand-name {
    font-family: "Oswald", sans-serif;
    font-weight: 700;
    font-size: 44px;
    letter-spacing: 2px;
    color: var(--silver);
    text-transform: uppercase;
    line-height: 1.02;
  }
  .brand-name span { display: block; }
  .highlights {
    position: absolute;
    left: 60px;
    right: 60px;
    bottom: 38px;
    list-style: none;
    display: grid;
    grid-template-columns: 1fr 1fr;
    gap: 8px 24px;
  }
  .highlights li {
    display: flex;
    align-items: center;
    gap: 9px;
    font-size: 14px;
    letter-spacing: 0.4px;
    color: var(--silver-soft);
    white-space: nowrap;
  }
  .highlights li::before {
    content: "";
    flex: none;
    width: 6px;
    height: 6px;
    border-radius: 50%;
    background: var(--silver-soft);
  }
  /* Back */
  .watermark {
    position: absolute;
    left: 150px;
    top: 80px;
    width: 240px;
    height: 240px;
    border-radius: 50%;
    background: radial-gradient(circle at 40% 40%, #242426, #121213 70%);
  }
  .person {
    position: absolute;
    left: 60px;
    top: 150px;
  }
  .person-name {
    font-family: "Oswald", sans-serif;
    font-weight: 700;
    font-size: 34px;
    letter-spacing: 1px;
    color: var(--gloss-text);
    text-shadow: 0 1px 0 #0a0a0a, 0 -1px 0 #707075;
    text-transform: uppercase;
  }
  .person-role {
    font-size: 17px;
    color: var(--muted);
    text-align: right;
    margin-top: -4px;
  }
  .contact {
    position: absolute;
    left: 360px;
    top: 195px;
    list-style: none;
    display: flex;
    flex-direction: column;
    gap: 8px;
  }
  .contact li {
    display: flex;
    align-items: center;
    gap: 10px;
    font-size: 18px;
    color: var(--silver);
    letter-spacing: 0.5px;
  }
  .contact svg { width: 13px; height: 13px; fill: var(--silver-soft); flex: none; }
  .address {
    position: absolute;
    left: 60px;
    bottom: 50px;
    font-size: 18px;
    letter-spacing: 1px;
    color: var(--gloss-text);
    text-shadow: 0 -1px 0 #77777c;
  }
</style>
</head>
<body>
  <section class="card card-front">
    <div class="brand">
      <span class="brand-dot"></span>
      <span class="brand-name"><span>Ridgeline</span><span>Funding</span></span>
    </div>
    <ul class="highlights">
      <li>$250,000 Application Only Program</li>
      <li>Loans from $30,000 to $5,000,000</li>
      <li>Competitive Interest Rates</li>
      <li>100% Financing</li>
    </ul>
  </section>

  <section class="card card-back">
    <div class="watermark" role="img" aria-label="Faint gloss brand emblem"></div>
    <div class="person">
      <div class="person-name">Jordan Hale</div>
      <div class="person-role">Director</div>
    </div>
    <ul class="contact">
      <li>
        <svg viewBox="0 0 24 24" aria-hidden="true"><path d="M6.6 10.8a15 15 0 0 0 6.6 6.6l2.2-2.2c.3-.3.7-.4 1-.2 1.1.4 2.3.6 3.6.6.6 0 1 .4 1 1V20c0 .6-.4 1-1 1A17 17 0 0 1 3 4c0-.6.4-1 1-1h3.5c.6 0 1 .4 1 1 0 1.3.2 2.5.6 3.6.1.3 0 .7-.2 1z"/></svg>
        1300 555 014
      </li>
      <li>
        <svg viewBox="0 0 24 24" aria-hidden="true"><path d="M2 5h20v14H2zm2 2v.5l8 5 8-5V7zm0 3v7h16v-7l-8 5z"/></svg>
        info@ridgelinefunding.com
      </li>
      <li>
        <svg viewBox="0 0 24 24" aria-hidden="true"><path d="M12 2a10 10 0 1 0 0 20 10 10 0 0 0 0-20zm6.9 6h-3a15 15 0 0 0-1.3-3.9A8 8 0 0 1 18.9 8zM12 4c.8 1.2 1.5 2.5 1.9 4h-3.8c.4-1.5 1.1-2.8 1.9-4zM4.3 14a8 8 0 0 1 0-4h3.4a16 16 0 0 0 0 4zm.8 2h3a15 15 0 0 0 1.3 3.9A8 8 0 0 1 5.1 16zm3-8h-3a8 8 0 0 1 4.3-3.9C8.8 5.3 8.4 6.6 8.1 8zM12 20c-.8-1.2-1.5-2.5-1.9-4h3.8c-.4 1.5-1.1 2.8-1.9 4zm2.3-6H9.7a14 14 0 0 1 0-4h4.6a14 14 0 0 1 0 4zm.3 5.9c.6-1.2 1-2.5 1.3-3.9h3a8 8 0 0 1-4.3 3.9zm1.7-5.9a16 16 0 0 0 0-4h3.4a8 8 0 0 1 0 4z"/></svg>
        www.ridgelinefunding.com
      </li>
    </ul>
    <p class="address">2150 Harbor Mill Rd. Plano, TX 75093</p>
  </section>
</body>
</html>
```